Flyer Design Project for a Seminar "Crossing The Far Bridge"

KTMV Chartered Accountants would like a flyer invitation designed for our upcoming seminar "Crossing The Far Bridge." The invitation should be created in MS Word, for editing capabilities on our end.

Seminar Title: "Crossing The Far Bridge: Securing and Growing Worth Across A Company Handover"

This is a complimentary breakfast seminar for Owners and CEOs of private corporations with revenues ranging from $2M to $150M.

Please leave substantial room to enter overview information on the seminar and topics of discussion.

We are open to bold colours and interesting graphics.

An example of a very amateur in-house design is attached.

Target Market(s)

Business owners and CEOs (typically men between 40 and 50 years old)

Industry/Entity Type

Business

Requirements
Must have
• -Substantial space to enter overview info about the seminar
-Space to enter logistical info about the seminar (i.e When, Where and RSVP info)
-Text should be Gill Sans. 1 page only
Should not have
• Stock photos of fake office people or American dollars (we are a Canadian company)!

```html
<!DOCTYPE html>
<html lang="en">
<head>
<meta charset="utf-8">
<title>Crossing The Far Bridge – Seminar Invitation</title>
<link rel="stylesheet" href="https://fonts.googleapis.com/css2?family=Cabin:wght@400;500;600;700&display=swap">
<style>
  :root {
    --ink: #2b2b2b;
    --ink-soft: #4a4a4a;
    --orange: #f9b040;
    --gold: #e4a232;
    --red: #d42a2a;
    --red-dark: #a81c1c;
    --band-red: #ee1c25;
    --band-yellow: #fff200;
    --band-green: #8dc63f;
    --card-light: #fbf3ea;
    --card-mid: #f1e2d2;
    --paper: #ffffff;
  }
  * { box-sizing: border-box; margin: 0; padding: 0; }
  html, body { width: 1200px; height: 927px; overflow: hidden; background: var(--paper); }
  body { font-family: "Cabin", "Gill Sans", sans-serif; color: var(--ink); }
  .flyer { position: relative; width: 1200px; height: 927px; }

  .title-banner {
    position: absolute; left: 131px; top: 55px; width: 591px; height: 63px;
    background: var(--orange); border-radius: 10px;
    display: flex; align-items: center; justify-content: center;
  }
  .title-banner h1 {
    font-size: 33px; font-weight: 700; letter-spacing: 2px; color: #fff;
    text-shadow: 1px 2px 2px rgba(0,0,0,.35);
  }
  .subtitle {
    position: absolute; left: 60px; width: 720px; top: 128px; text-align: center;
    font-size: 18px; font-weight: 700; color: var(--gold); letter-spacing: .4px;
    text-shadow: 1px 1px 1px rgba(0,0,0,.3);
  }
  .intro {
    position: absolute; left: 60px; width: 735px; top: 183px; text-align: center;
    font-size: 16.5px; line-height: 27px; color: var(--ink);
  }
  .overview {
    position: absolute; left: 65px; width: 760px; top: 332px;
    font-size: 15.5px; line-height: 27px; color: var(--ink-soft);
    letter-spacing: .3px; white-space: nowrap;
  }
  .overview strong { font-weight: 500; color: var(--ink); }
  .overview p { margin-bottom: 7px; }
  .overview h2 { font-size: 15.5px; font-weight: 500; color: var(--ink); margin-top: 0; }
  .topics { list-style: none; margin: 6px 0 0 38px; }
  .topics li { position: relative; padding-left: 10px; line-height: 31px; }
  .topics li::before {
    content: ""; position: absolute; left: 0; top: 13px; width: 6px; height: 6px;
    border-radius: 50%; background: var(--band-green);
  }
  .topics .wrap { padding-left: 18px; }
  .overview .closing { margin-top: 13px; margin-bottom: 0; }

  .info-card { position: absolute; left: 808px; width: 327px; height: 70px; }
  .info-card .panel {
    position: absolute; left: 34px; right: 0; top: 0; bottom: 0; border-radius: 10px;
    background: linear-gradient(180deg, var(--card-light), var(--card-mid));
    box-shadow: 0 2px 3px rgba(0,0,0,.12);
    padding: 10px 14px 0 56px; font-size: 15px; line-height: 18px; color: #111;
  }
  .info-card .badge {
    position: absolute; left: 0; top: 50%; width: 76px; height: 76px; margin-top: -38px;
    border-radius: 50%; background: radial-gradient(circle at 40% 35%, #e5413a, var(--red-dark));
    border: 3px solid #f3d8d2; box-shadow: 0 2px 4px rgba(0,0,0,.3);
    display: flex; align-items: center; justify-content: center;
    color: #fff; font-size: 18px; font-weight: 500;
  }
  .card-when { top: 173px; }
  .card-when .panel { text-align: center; padding-left: 60px; padding-top: 12px; }
  .card-where { top: 270px; height: 68px; }
  .card-rsvp { top: 377px; height: 72px; }
  .card-remark { top: 478px; height: 78px; }
  .card-remark .panel { padding-top: 6px; }
  .card-rsvp a { color: #111; }

  .signpost {
    position: absolute; left: 885px; top: 565px; width: 205px; height: 162px;
    border-radius: 8px;
    background: linear-gradient(135deg, #f5a73c 0%, #f3e6c4 40%, #8fb9d8 70%, #8dc63f 100%);
  }

  .partner {
    position: absolute; top: 832px; width: 220px; text-align: center;
    font-size: 15px; font-weight: 600; color: var(--ink); white-space: nowrap;
  }
  .partner-firm { left: 152px; }
  .partner-capital { left: 415px; }

  .color-band { position: absolute; top: 878px; height: 22px; }
  .band-red { left: 65px; width: 342px; background: var(--band-red); }
  .band-yellow { left: 407px; width: 472px; background: var(--band-yellow); }
  .band-green { left: 879px; width: 254px; background: var(--band-green); }
</style>
</head>
<body>
<main class="flyer">
  <header class="title-banner"><h1>Crossing The Far Bridge</h1></header>
  <p class="subtitle">Securing and Growing Worth Across A Company Handover</p>

  <p class="intro">
    A complimentary breakfast seminar for Owners and CEOs of private corporations<br>
    with revenues ranging from $2M to $150M.<br>
    Thursday, February 24, 2011<br>
    7:45 – 10:00 AM
  </p>

  <section class="overview">
    <p>Almost <strong>two-thirds of independent business owners</strong> in Canada are planning to exit their<br>business within the next decade. &nbsp;&nbsp;The spoils will go to those who have planned in advance.<br>Are you one of them?</p>
    <p>Join Martin Ellery, Partner at KTMV Chartered Accountants, and Paul Desrochers, Co-Founder of<br>Northvale Capital Partners, for a compelling overview of one of the most critical issues affecting<br>privately-held businesses today.</p>
    <h2>Topics of discussion will include:</h2>
    <ul class="topics">
      <li>The alternatives for exiting a business and the implications of each</li>
      <li>Tax minimization strategies for the sale/transfer of your business</li>
      <li>Tactics for gaining control of the deal to achieve a successful sale and maximize the value<br><span class="wrap">you receive from it</span></li>
      <li>Real-life case studies and lessons to be learned from them</li>
    </ul>
    <p class="closing">All attendees will receive detailed seminar handouts and a complimentary consultation with<br>both Martin and Paul to map out the next steps in developing an effective exit plan for their<br>business.</p>
  </section>

  <aside class="info-card card-when">
    <div class="panel">Thursday, February 24, 2011<br><br>7:45 – 10:00 AM</div>
    <div class="badge">When</div>
  </aside>
  <aside class="info-card card-where">
    <div class="panel">KTMV Chartered Accountants<br>1180 Harlow Avenue, Suite 300<br>Toronto</div>
    <div class="badge">Where</div>
  </aside>
  <aside class="info-card card-rsvp">
    <div class="panel">Contact Claire Beaudoin<br>at 416.555.0190 x 212 or<br><a href="mailto:events@ktmv.ca">events@ktmv.ca</a></div>
    <div class="badge">RSVP</div>
  </aside>
  <aside class="info-card card-remark">
    <div class="panel">Pre-registration is required!<br>Seats are limited and will be<br>reserved on a first-come,<br>first-served basis.</div>
    <div class="badge">Remark</div>
  </aside>

  <div class="signpost" role="img" aria-label="Illustration of a signpost with many colourful arrows pointing different ways, each marked Exit"></div>

  <div class="partner partner-firm">KTMV Chartered Accountants</div>
  <div class="partner partner-capital">Northvale Capital Partners</div>

  <div class="color-band band-red"></div>
  <div class="color-band band-yellow"></div>
  <div class="color-band band-green"></div>
</main>
</body>
</html>
```